Health Care Company with Logo Needs Business Cards designed

We are a luxury behavioral health company looking for business cards design we already have a logo and are looking for someone to design a sophisticated luxurious looking business card. Please note that Card design should be captivating just like the logo and also encompass the logo color

Industry/Entity Type

Healthcare

Contact Information for Business Card

Logo,company name, tagline, my name and title, contact details, and physical address

```html
<!DOCTYPE html>
<html lang="en">
<head>
<meta charset="utf-8">
<title>Orrin Mind Care – Business Cards</title>
<link rel="stylesheet" href="https://fonts.googleapis.com/css2?family=Archivo:wght@400;500;800&family=Roboto+Condensed:wght@700&display=swap">
<style>
  :root {
    --backdrop: #2b2b2b;
    --black: #000000;
    --purple: #7b3f98;
    --blue: #00aeef;
    --green: #8dc63f;
    --orange: #f7941d;
    --white: #ffffff;
    --ink: #111111;
    --soft: #d9d9d9;
  }
  * { box-sizing: border-box; margin: 0; padding: 0; }
  html, body {
    width: 1200px; height: 1015px; overflow: hidden;
    background: var(--backdrop);
    font-family: "Archivo", Arial, sans-serif;
  }
  .canvas { position: relative; width: 1200px; height: 1015px; }

  .card {
    position: absolute; left: 220px; width: 760px; height: 434px;
    overflow: hidden; box-shadow: 0 14px 30px rgba(0,0,0,.55);
  }
  .card--back { top: 48px; background: var(--black); }
  .card--front { top: 532px; background: var(--white); }

  .edge-band { position: absolute; left: 0; right: 0; bottom: 0; height: 14px; display: flex; }
  .edge-band__orange { flex: 0 0 50%; background: var(--orange); }
  .edge-band__green { flex: 1; background: var(--green); margin-left: 4px; }

  .brand { display: flex; align-items: center; gap: 18px; }
  .brand__mark { width: 46px; height: 46px; background: var(--green); flex: none; }
  .brand__name { font-weight: 800; font-size: 42px; line-height: 1; }
  .brand__tagline { margin-top: 8px; font-weight: 400; font-size: 17px; }

  .card--back .brand { position: absolute; left: 170px; top: 178px; }
  .card--back .brand__name { color: var(--white); }
  .card--back .brand__tagline { color: var(--soft); }

  .front__purple { position: absolute; left: 0; right: 0; top: 0; height: 215px; background: var(--purple); }
  .front__blue { position: absolute; left: 0; right: 0; top: 215px; height: 125px; background: var(--blue); }
  .card--front .brand { position: absolute; left: 70px; top: 108px; }
  .card--front .brand__name { color: var(--white); font-size: 40px; }
  .card--front .brand__tagline { color: var(--white); }

  .person { position: absolute; left: 70px; top: 236px; color: var(--white); }
  .person__name { font-family: "Roboto Condensed", Arial, sans-serif; font-weight: 700; font-size: 40px; line-height: 1; }
  .person__title { font-size: 22px; margin-top: 4px; }

  .divider { position: absolute; left: 365px; top: 232px; width: 2px; height: 90px; background: var(--white); }

  .contacts { position: absolute; left: 392px; top: 234px; list-style: none; color: var(--white); font-size: 20px; }
  .contacts li { display: flex; align-items: center; gap: 12px; height: 28px; }
  .contacts svg { width: 20px; height: 20px; flex: none; }

  .address { position: absolute; left: 70px; top: 358px; font-size: 23px; color: var(--ink); }
</style>
</head>
<body>
<main class="canvas">

  <section class="card card--back" aria-label="Business card back">
    <div class="brand">
      <span class="brand__mark"></span>
      <div>
        <div class="brand__name">Orrin Mind Care</div>
        <div class="brand__tagline">Steady support for every step</div>
      </div>
    </div>
    <div class="edge-band"><span class="edge-band__orange"></span><span class="edge-band__green"></span></div>
  </section>

  <section class="card card--front" aria-label="Business card front">
    <div class="front__purple"></div>
    <div class="front__blue"></div>

    <div class="brand">
      <span class="brand__mark"></span>
      <div>
        <div class="brand__name">Orrin Mind Care</div>
        <div class="brand__tagline">Steady support for every step</div>
      </div>
    </div>

    <div class="person">
      <div class="person__name">Daniel Reyes</div>
      <div class="person__title">Managing Director</div>
    </div>

    <span class="divider"></span>

    <ul class="contacts">
      <li>
        <svg viewBox="0 0 24 24" fill="none" stroke="currentColor" stroke-width="2.2" stroke-linecap="round"><path d="M5 3h4l2 5-2.5 1.5a11 11 0 0 0 6 6L16 13l5 2v4a2 2 0 0 1-2 2A17 17 0 0 1 3 5a2 2 0 0 1 2-2z"/></svg>
        044-555 010 234
      </li>
      <li>
        <svg viewBox="0 0 24 24" fill="none" stroke="currentColor" stroke-width="2"><rect x="2" y="5" width="20" height="14"/><path d="M2 5l10 8 10-8"/></svg>
        info@orrinmindcare.com
      </li>
      <li>
        <svg viewBox="0 0 24 24" fill="none" stroke="currentColor" stroke-width="1.8"><circle cx="12" cy="12" r="10"/><ellipse cx="12" cy="12" rx="4.5" ry="10"/><path d="M2 12h20M4 7h16M4 17h16"/></svg>
        www.orrinmindcare.com
      </li>
    </ul>

    <p class="address">218, Willow Park Lane 30718, Eastbrook</p>

    <div class="edge-band"><span class="edge-band__orange"></span><span class="edge-band__green"></span></div>
  </section>

</main>
</body>
</html>
```